Payday Lending App Interface Design

Hello, we are building a payday lending application, Lendoro, that lend people money. I have drafted some of the screens that show the functionalities we have at the moment, please find the screens in attachments.
The elements in the screens are placed just to show what should be included in those screens, it's not necessary to follow the same layout. If you have better design ideas, you are very welcomed to show off your talent.
I think what we want is a style guide so that we can apply the same style to any screens that are similar to the ones I attached. We really like
the style as in the attached image called Style.png. We might want something similar - a simple, clean design yet fun and engaging. Customised graphical elements such as icons, illustrations are preferable.
Apart from the attached screens, we might also need a design for the On Board screen and the Login/Sign Up screen too.
Our logo colour is in yellow and black. Perhaps we will have a similar colour theme. I also attached the logo file, icon-Lendoro.png, if you would like to put it in your design.
Please message me if you need further information.
Regards
Target Market(s)
Young people that doesn't have strong income

```html
<!DOCTYPE html>
<html lang="en">
<head>
<meta charset="utf-8">
<title>Lendoro – App Screens</title>
<link href="https://fonts.googleapis.com/css2?family=Poppins:wght@400;500;600;700&display=swap" rel="stylesheet">
<style>
:root{
  --stage:#2b2b2b;
  --yellow:#fad40f;
  --yellow-deep:#dbb300;
  --cream:#fdf3c2;
  --beige:#e3dcbc;
  --ink:#141414;
  --ink-soft:#2b2b2b;
  --white:#ffffff;
  --grey-panel:#e8e8e8;
  --tile:#f2f2f2;
  --red-name:#e8101b;
  --blue-name:#1a6ef2;
  --gold-name:#f2c400;
}
*{box-sizing:border-box;margin:0;padding:0}
html,body{width:1200px;height:493px;overflow:hidden;background:var(--stage);font-family:'Poppins',sans-serif;color:var(--ink)}
.screen{position:absolute;top:26px;width:277px;height:432px;overflow:hidden;background:var(--cream)}
.screen--connect{left:16px;background:var(--yellow)}
.screen--loan{left:307px}
.screen--bank{left:599px}
.screen--personal{left:890px}
.decor{position:absolute;inset:0;width:277px;height:432px}
.appbar{position:absolute;top:0;left:0;width:277px;height:46px;background:var(--yellow);border-radius:0 0 9px 9px;display:flex;align-items:center;justify-content:center;font-weight:600;font-size:12px;letter-spacing:.3px;z-index:2}
.appbar svg{position:absolute;left:10px;top:17px}
.brand-tile{position:absolute;left:91px;top:44px;width:96px;height:96px;background:var(--white);border-radius:20px;display:flex;align-items:center;justify-content:center;font-weight:700;font-size:17px}
.connect-title{position:absolute;left:10px;top:241px;font-weight:700;font-size:21px;line-height:27px}
.connect-note{position:absolute;left:10px;top:302px;width:262px;font-size:10.4px;line-height:18px}
.btn{position:absolute;left:10px;width:258px;height:40px;border-radius:20px;display:flex;align-items:center;justify-content:center;font-weight:600;font-size:11px;letter-spacing:.4px}
.btn--black{background:#000;color:var(--white)}
.btn--dark{background:var(--ink-soft);color:var(--white)}
.btn--yellow{background:var(--yellow);color:var(--ink);gap:8px}
.label{position:absolute;left:10px;font-weight:600;font-size:12.4px;line-height:16px}
.amount-big{position:absolute;left:10px;top:92px;font-weight:700;font-size:35px;line-height:40px;color:var(--yellow);letter-spacing:1px}
.progress{position:absolute;left:10px;top:163px;width:258px;height:12px;background:var(--white);border-radius:6px;font-size:8px;display:flex}
.progress__paid{width:131px;background:var(--yellow);border-radius:6px;text-align:center;line-height:12px}
.progress__left{flex:1;text-align:center;line-height:12px}
.progress-legend{position:absolute;top:181px;left:9px;width:260px;display:flex;justify-content:space-between;font-size:9.8px;line-height:12px}
.activities{position:absolute;left:0;top:216px;width:277px;height:216px;background:var(--grey-panel);border-radius:9px 9px 0 0}
.activity{position:absolute;left:10px;width:258px;height:47px;background:var(--white);border-radius:6px;padding:7px 14px}
.activity__title{font-weight:600;font-size:11px;line-height:15px}
.activity__date{font-size:8px;margin-top:4px}
.activity__amount{position:absolute;right:14px;top:15px;font-weight:600;font-size:11.5px}
.bank-card{position:absolute;left:10px;width:258px;height:65px;background:var(--white);border-radius:8px}
.bank-card__tile{position:absolute;left:7px;top:6px;width:53px;height:53px;background:var(--tile);border-radius:7px}
.bank-card__name{position:absolute;left:73px;top:16px;font-weight:600;font-size:12.4px;line-height:14px}
.bank-card__number{position:absolute;left:73px;top:33px;font-size:10.8px}
.bank-card__more{position:absolute;right:12px;top:30px}
.name--red{color:var(--red-name)}
.name--blue{color:var(--blue-name)}
.name--gold{color:var(--gold-name)}
.hint{position:absolute;left:10px;top:64px;font-size:10.4px}
.field{position:absolute;left:10px;width:258px;height:40px;background:var(--white);border-radius:20px;padding-left:13px;display:flex;align-items:center;font-size:10.4px}
</style>
</head>
<body>

<section class="screen screen--connect">
  <svg class="decor" viewBox="0 0 277 432" aria-hidden="true">
    <circle cx="240" cy="385" r="236" fill="var(--yellow-deep)"/>
    <circle cx="252" cy="345" r="100" fill="var(--yellow)"/>
  </svg>
  <div class="brand-tile">Lendoro</div>
  <h1 class="connect-title">Connecting<br>to your bank.....</h1>
  <p class="connect-note">Please don't exit the app. !Makes 3-5 minutes to confirm your details with your bank</p>
  <div class="btn btn--black" style="top:358px">NEXT</div>
</section>

<section class="screen screen--loan">
  <svg class="decor" viewBox="0 0 277 432" aria-hidden="true">
    <circle cx="330" cy="330" r="190" fill="#fbeaa8"/>
    <circle cx="330" cy="330" r="140" fill="var(--beige)"/>
  </svg>
  <header class="appbar">
    <svg width="8" height="12" viewBox="0 0 8 12"><path d="M6 1 1.5 6 6 11" fill="none" stroke="#141414" stroke-width="2.2" stroke-linecap="round" stroke-linejoin="round"/></svg>
    LOAN DETAILS
  </header>
  <div class="label" style="top:64px">Next Repayment</div>
  <div class="amount-big">$XX</div>
  <div class="label" style="top:131px">On 4 Dec</div>
  <div class="progress"><span class="progress__paid">xxx</span><span class="progress__left">xxx</span></div>
  <div class="progress-legend"><span>Paid</span><span>Left</span></div>
  <div class="activities">
    <div class="label" style="top:14px">Activities</div>
    <div class="activity" style="top:39px"><div class="activity__title">Repayment</div><div class="activity__date">DD /MM/YY</div><div class="activity__amount">$XX</div></div>
    <div class="activity" style="top:94px"><div class="activity__title">Repayment</div><div class="activity__date">DD /MM/YY</div><div class="activity__amount">$XX</div></div>
    <div class="activity" style="top:150px"><div class="activity__title">Repayment</div><div class="activity__date">DD /MM/YY</div><div class="activity__amount">$XX</div></div>
  </div>
</section>

<section class="screen screen--bank">
  <svg class="decor" viewBox="0 0 277 432" aria-hidden="true">
    <circle cx="240" cy="420" r="200" fill="var(--beige)"/>
    <circle cx="240" cy="420" r="110" fill="var(--cream)"/>
  </svg>
  <header class="appbar">
    <svg width="8" height="12" viewBox="0 0 8 12"><path d="M6 1 1.5 6 6 11" fill="none" stroke="#141414" stroke-width="2.2" stroke-linecap="round" stroke-linejoin="round"/></svg>
    BANK DETIALS
  </header>
  <div class="bank-card" style="top:67px">
    <div class="bank-card__tile"></div>
    <div class="bank-card__name name--red">Harbor Savings</div>
    <div class="bank-card__number">1287687965865688</div>
    <svg class="bank-card__more" width="12" height="4" viewBox="0 0 12 4"><circle cx="2" cy="2" r="1.6"/><circle cx="6" cy="2" r="1.6"/><circle cx="10" cy="2" r="1.6"/></svg>
  </div>
  <div class="bank-card" style="top:144px">
    <div class="bank-card__tile"></div>
    <div class="bank-card__name name--blue">Northvale</div>
    <div class="bank-card__number">1287687965865688</div>
    <svg class="bank-card__more" width="12" height="4" viewBox="0 0 12 4"><circle cx="2" cy="2" r="1.6"/><circle cx="6" cy="2" r="1.6"/><circle cx="10" cy="2" r="1.6"/></svg>
  </div>
  <div class="bank-card" style="top:220px">
    <div class="bank-card__tile"></div>
    <div class="bank-card__name name--gold">Meridian Bank</div>
    <div class="bank-card__number">1287687965865688</div>
    <svg class="bank-card__more" width="12" height="4" viewBox="0 0 12 4"><circle cx="2" cy="2" r="1.6"/><circle cx="6" cy="2" r="1.6"/><circle cx="10" cy="2" r="1.6"/></svg>
  </div>
  <div class="btn btn--yellow" style="top:374px">
    <svg width="11" height="11" viewBox="0 0 11 11"><circle cx="5.5" cy="5.5" r="5.5" fill="#141414"/><path d="M5.5 3v5M3 5.5h5" stroke="#fad40f" stroke-width="1.4"/></svg>
    CONNECT BANK ACCOUNT
  </div>
</section>

<section class="screen screen--personal">
  <svg class="decor" viewBox="0 0 277 432" aria-hidden="true">
    <circle cx="260" cy="380" r="200" fill="var(--beige)"/>
    <circle cx="260" cy="380" r="110" fill="var(--cream)"/>
  </svg>
  <header class="appbar">
    <svg width="8" height="12" viewBox="0 0 8 12"><path d="M6 1 1.5 6 6 11" fill="none" stroke="#141414" stroke-width="2.2" stroke-linecap="round" stroke-linejoin="round"/></svg>
    PERSONAL DETIALS
  </header>
  <p class="hint">Please provide detials as shown on ID</p>
  <div class="field" style="top:97px">Given Name</div>
  <div class="field" style="top:146px">Middle Name</div>
  <div class="field" style="top:195px">Surname</div>
  <div class="field" style="top:243px">Date of Birth (Day/ Month/ Year)</div>
  <div class="btn btn--dark" style="top:297px">NEXT</div>
</section>

</body>
</html>
```